Existing Website Requiring new Pages

I have an existing word press website that was built using elementor.
Website: www.tallowcrestcare.com.au
I require the Vacancies page (https://www.tallowcrestcare.com.au/vacancies/) to be modified to display our new properties along with minor tweaks to how the information is presented.
The vacancies to be displayed are the exactly the same as those that are located on the homepage of QMR website (https://qmr.org.au/)
The new pages that link off the Vacancies tab will require custom design.
There are roughly 8 pages/properties to be incorporated. i wish for the design to be very similar to that displayed in the following link; https://www.polunda.com.au/vacancies/merrylands
Along with this the back end has not been updated for the last 3 years so it also requires some maintenance.
Website is in the disability industry and the custom pages will display information relative to Property Vacancies.
I have attached a ZIP file with some design guides, the information for each of the properties (which will need to be modified to show our business name Tallowcrest Care) and the example of how it is to look based off the Polunda website.
If you guys have any suggestions or ideas on how to make this more presentable or possible i'm open to your ideas.
Target Market(s)
People looking for SDA properties custom built for people with a disability
Industry/Entity Type
Disability
Coding
Coded - Design and coding required
Number of Pages Required
5+ page

```html
<!DOCTYPE html>
<html lang="en">
<head>
<meta charset="utf-8">
<title>Tallowcrest Care – SDA Vacancies</title>
<link href="https://fonts.googleapis.com/css2?family=Poppins:wght@400;500;600;700&display=swap" rel="stylesheet">
<style>
:root{
  --pink:#e6498d;
  --pink-soft:#f9d2e4;
  --ink:#1e1e1e;
  --muted:#555;
  --line:#d9d9d9;
  --grey-bg:#efefef;
  --hero-dark:#2b2a28;
  --social:#4a3f7a;
}
*{box-sizing:border-box;margin:0;padding:0}
html,body{width:1200px;height:2548px;overflow:hidden}
body{font-family:"Poppins",sans-serif;color:var(--ink);background:#fff;position:relative}
.site-header{height:140px;display:flex;align-items:center;justify-content:space-between;padding:0 40px 0 100px}
.brand{display:flex;align-items:center;gap:12px}
.brand-dot{width:40px;height:40px;border-radius:50%;background:var(--pink)}
.brand-name{font-weight:600;font-size:20px;color:var(--pink)}
.main-nav{display:flex;gap:34px;font-size:13px;font-weight:500;letter-spacing:.3px}
.main-nav a{color:var(--ink);text-decoration:none}
.main-nav a.active{color:var(--pink)}
.hero{position:absolute;top:140px;left:0;width:1200px;height:492px;background:linear-gradient(90deg,#1c1b1a 0%,#3a3835 45%,#6c6a66 75%,#4a4845 100%)}
.hero-content{position:absolute;left:100px;top:96px;color:#fff}
.hero h1{font-size:38px;font-weight:600;line-height:1.2;width:560px}
.hero p{font-size:16px;line-height:1.45;width:540px;margin-top:18px;color:#eee}
.search{display:flex;align-items:flex-end;gap:20px;margin-top:46px}
.field label{display:block;font-size:15px;margin-bottom:10px}
.select{width:210px;height:48px;border:1px solid #aaa;background:rgba(255,255,255,.08);color:#ddd;font-size:13px;padding:0 14px;display:flex;align-items:center}
.btn{background:var(--pink);color:#fff;font-weight:500;font-size:14px;border:none;display:flex;align-items:center;justify-content:center}
.search .btn{width:140px;height:48px}
.vacancies{position:absolute;top:632px;left:100px;width:1000px}
.vacancies h2{font-size:24px;font-weight:600;margin-top:88px}
.cards{display:grid;grid-template-columns:repeat(3,320px);column-gap:20px;row-gap:24px;margin-top:50px}
.card-img{height:208px}
.card-head{display:flex;justify-content:space-between;align-items:center;margin-top:20px}
.card-title{font-size:15px;font-weight:600}
.badge{font-size:11px;background:#eee;border:1px solid #ccc;padding:2px 8px}
.card-sub{font-size:13px;color:var(--muted);margin-top:10px}
.card .btn{height:44px;margin-top:16px;background:var(--pink-soft);color:var(--pink);font-size:14px}
.load-more{width:132px;height:44px;margin:44px auto 0}
.contact{position:absolute;top:1700px;left:0;width:1200px;height:560px;background:var(--grey-bg)}
.contact h2{position:absolute;left:100px;top:36px;font-size:24px;font-weight:600}
.map{position:absolute;left:100px;top:80px;width:412px;height:412px;background:linear-gradient(135deg,#e8e4dc,#d6dde0 60%,#cfd8d4)}
.form{position:absolute;left:584px;top:86px;width:516px}
.row{display:flex;gap:20px}
.row .group{flex:1}
.group{margin-bottom:18px}
.group label{display:block;font-size:15px;font-weight:500;margin-bottom:8px}
.input{height:48px;background:#fff;border:1px solid var(--line);font-size:13px;color:#888;padding:0 14px;display:flex;align-items:center}
.textarea{height:104px;align-items:flex-start;padding-top:14px}
.form .btn{height:44px;width:100%}
.site-footer{position:absolute;top:2260px;left:0;width:1200px;height:288px}
.footer-brand{position:absolute;left:100px;top:60px}
.footer-brand .brand-name{font-size:24px}
.footer-contact{position:absolute;left:100px;top:212px;font-size:12px;color:var(--muted);line-height:20px}
.footer-contact div{display:flex;align-items:center;gap:8px}
.socials{position:absolute;left:520px;top:58px;display:flex;flex-direction:column;gap:14px}
.socials span{width:28px;height:28px;border-radius:50%;background:var(--social);display:block}
.socials span:first-child{background:#7d4bb0}
.footer-col{position:absolute;top:48px;font-size:12px;color:var(--muted)}
.footer-col h3{font-size:14px;font-weight:600;color:var(--ink);border-left:3px solid var(--pink);padding-left:10px;margin-bottom:18px}
.footer-col li{list-style:none;line-height:28px;border-bottom:1px solid #eee;width:220px}
</style>
</head>
<body>
<header class="site-header">
  <div class="brand"><span class="brand-dot"></span><span class="brand-name">Tallowcrest Care</span></div>
  <nav class="main-nav">
    <a class="active" href="#">HOME</a><a href="#">ABOUT US</a><a href="#">WHAT WE DO ▾</a><a href="#">REFERRALS</a><a href="#">FEEDBACK</a><a href="#">CONTACT US</a>
  </nav>
</header>

<section class="hero" role="img" aria-label="Modern accessible kitchen interior">
  <div class="hero-content">
    <h1>Your Dream Home Awaits at SDA Homes</h1>
    <p>Discover exceptional living spaces that seamlessly blend style, comfort, and accessibility.</p>
    <div class="search">
      <div class="field"><label>Location</label><div class="select">All Suburbs</div></div>
      <div class="field"><label>Design Category</label><div class="select">All Categories</div></div>
      <div class="btn">Search Now</div>
    </div>
  </div>
</section>

<section class="vacancies">
  <h2>SDA vacancies and homes</h2>
  <div class="cards">
    <article class="card"><div class="card-img" role="img" aria-label="Modern kitchen of the Austral home" style="background:linear-gradient(160deg,#e9ece8,#9aa49a)"></div><div class="card-head"><span class="card-title">SDA in Austral</span><span class="badge">4 Bedroom</span></div><p class="card-sub">Fully Accessible, High Physical Support</p><div class="btn">See Detail</div></article>
    <article class="card"><div class="card-img" role="img" aria-label="Brick townhouses in Merrylands" style="background:linear-gradient(170deg,#bcd2e6,#9c7a5e 60%,#6d5a4b)"></div><div class="card-head"><span class="card-title">SDA in Merrylands</span><span class="badge">4 Bedroom</span></div><p class="card-sub">Fully Accessible, High Physical Support</p><div class="btn">See Detail</div></article>
    <article class="card"><div class="card-img" role="img" aria-label="Two-storey home in Guildford West" style="background:linear-gradient(170deg,#a9c8e8,#c9c3ba 55%,#8b8479)"></div><div class="card-head"><span class="card-title">SDA in Guildford West</span><span class="badge">4 Bedroom</span></div><p class="card-sub">Fully Accessible, High Physical Support</p><div class="btn">See Detail</div></article>
    <article class="card"><div class="card-img" role="img" aria-label="Brick units in Greystanes" style="background:linear-gradient(170deg,#b7d3ec,#b38a66 55%,#7c6a58)"></div><div class="card-head"><span class="card-title">SDA in Greystanes</span><span class="badge">4 Bedroom</span></div><p class="card-sub">Fully Accessible, High Physical Support</p><div class="btn">See Detail</div></article>
    <article class="card"><div class="card-img" role="img" aria-label="Modern home in Jordan Springs" style="background:linear-gradient(170deg,#b0cbe6,#a9a39b 55%,#6f6b66)"></div><div class="card-head"><span class="card-title">SDA in Jodan Springs</span><span class="badge">4 Bedroom</span></div><p class="card-sub">Fully Accessible, High Physical Support</p><div class="btn">See Detail</div></article>
    <article class="card"><div class="card-img" role="img" aria-label="Two-storey home in Werrington" style="background:linear-gradient(170deg,#b6d0ea,#d2cdc4 55%,#8e877d)"></div><div class="card-head"><span class="card-title">SDA in Werrington</span><span class="badge">4 Bedroom</span></div><p class="card-sub">Fully Accessible, High Physical Support</p><div class="btn">See Detail</div></article>
  </div>
  <div class="btn load-more">Load More</div>
</section>

<section class="contact">
  <h2>Contact Us</h2>
  <div class="map" role="img" aria-label="Street map showing office location"></div>
  <div class="form">
    <div class="row">
      <div class="group"><label>First Name</label><div class="input">Name</div></div>
      <div class="group"><label>Last Name</label><div class="input">Name</div></div>
    </div>
    <div class="group"><label>Email Address</label><div class="input">Your Email</div></div>
    <div class="group"><label>Massage</label><div class="input textarea">Write Massage</div></div>
    <div class="btn">Submit Now</div>
  </div>
</section>

<footer class="site-footer">
  <div class="footer-brand brand"><span class="brand-dot"></span><span class="brand-name">Tallowcrest Care</span></div>
  <div class="footer-contact">
    <div><svg width="10" height="10" viewBox="0 0 10 10"><rect x="0.5" y="1.5" width="9" height="7" fill="none" stroke="#e6498d"/><path d="M0.5 1.5 5 5.5 9.5 1.5" fill="none" stroke="#e6498d"/></svg>info@tallowcrestcare.com.au</div>
    <div><svg width="10" height="10" viewBox="0 0 10 10"><path d="M2 1 4 3 3 4.5Q4.5 6.5 5.5 7L7 6 9 8 7.5 9.5Q3 9 0.5 2.5Z" fill="#e6498d"/></svg>Phone: +61 2 9000 0000</div>
    <div><svg width="10" height="10" viewBox="0 0 10 10"><circle cx="5" cy="5" r="4.3" fill="none" stroke="#e6498d"/><path d="M5 2.5V5H7" fill="none" stroke="#e6498d"/></svg>Operating Hours: 9AM to 5PM Monday - Friday</div>
  </div>
  <div class="socials"><span></span><span></span><span></span><span></span><span></span></div>
  <div class="footer-col" style="left:608px">
    <h3>ACCOMMODATION</h3>
    <ul><li>Supported Independent Living (SIL)</li><li>Specialist Disability Accommodation (SDA)</li><li>Short-term Accommodation (Respite)</li><li>Vacancies</li></ul>
  </div>
  <div class="footer-col" style="left:872px">
    <h3>WHAT WE DO</h3>
    <ul><li>Disability Care</li><li>Social &amp; Community Services</li><li>Therapeutic Supports</li><li>Support Coordination</li><li>Home Modifications</li></ul>
  </div>
</footer>
</body>
</html>
```